Dog Snacks brand needs a new packaging design

Dear Designers,

We are looking for a packaging expert to design our new line of Dog Snacks which contain a relaxing hemp extract (CBD).

Our company is already selling various relaxing cat & dog products , and we would like this new design to reflect the same "style & feeling" as our current products (see attached instructions).

Technical aspects:
- The packaging is a Stand Up Pouch (12x18.5x7cm - see attached instructions).
- Please follow technical guidelines from printer (see attached instructions).
- The packaging will contain 120g of high-quality, semi-moist dog snacks.
- We will be designing 3 differents variations for 3 different flavours: Chicken, Beef & Liver.
- The packaging will be printed with a matt finish.

Design aspects:
- The design should be compatible with our brand identity (i.e. fluffly, pure, relaxing, positive, clean & natural).
- Soft/rounded shapes are preferred.
- Please use our brand's colors (#3BA384, White & Black).
- Please use our company logo (see attached instructions).
- The design also needs to convey a strong sense of professionalism as we are an animal "healthcare" brand.
- If you want to include a dog picture, we would prefer you to use a picture of our official brand ambassador (see attached instructions).
- We have attached a number of packaging examples which we like a lot. (see attached instructions). Please only use those as general inspiration.
- Only original work (no plagiarism will be accepted).

Please don't hesitate to send us a message if you have any questions about the brand, the product or the design requirements.

We look forward to seeing your designs & working on this together !

Thanks & regards,
Tobias

Target Market(s)

Dog owners

Industry/Entity Type

Pet Care

Font styles to use
Sans Serif

Requirements
Must have
• Please see project description.
Nice to have
Should not have

```html
<!DOCTYPE html>
<html lang="en">
<head>
<meta charset="utf-8">
<title>VerdaBites CBD Treats – Chicken Pouch</title>
<link href="https://fonts.googleapis.com/css2?family=Montserrat:wght@400;500;600;700&display=swap" rel="stylesheet">
<style>
  :root {
    --backdrop: #474747;
    --pouch-light: #eeeeee;
    --pouch-mid: #d9d9d9;
    --pouch-shadow: #c4c4c4;
    --brand-green: #3ba384;
    --brand-green-dark: #1f6b52;
    --ink: #1e1e1e;
    --ink-soft: #3a3a3a;
    --white: #ffffff;
  }
  * { margin: 0; padding: 0; box-sizing: border-box; }
  html, body { width: 1200px; height: 1200px; overflow: hidden; }
  body {
    background: var(--backdrop);
    font-family: "Montserrat", sans-serif;
    position: relative;
  }
  .pouch {
    position: absolute;
    left: 265px; top: 128px;
    width: 612px; height: 984px;
    border-radius: 34px 34px 10px 10px;
    background: linear-gradient(160deg, var(--pouch-light) 0%, var(--pouch-mid) 55%, var(--pouch-shadow) 100%);
    overflow: hidden;
  }
  .tear-notch {
    position: absolute; top: 152px; width: 10px; height: 18px;
    background: var(--backdrop);
  }
  .tear-notch.left { left: 0; border-radius: 0 9px 9px 0; }
  .tear-notch.right { right: 0; border-radius: 9px 0 0 9px; }
  .zip-line {
    position: absolute; left: 30px; right: 30px; top: 158px;
    height: 2px; background: rgba(0,0,0,0.08);
  }
  .tagline {
    position: absolute; top: 115px; width: 100%;
    text-align: center; font-size: 17px; font-weight: 500;
    letter-spacing: 1.5px; color: var(--ink);
  }
  .tagline .sep { margin: 0 6px; font-weight: 400; }
  .brand {
    position: absolute; top: 262px; width: 100%;
    display: flex; justify-content: center; align-items: center; gap: 14px;
  }
  .brand-dot {
    width: 22px; height: 22px; border-radius: 50%;
    background: var(--brand-green);
  }
  .brand-name {
    font-size: 46px; font-weight: 700; letter-spacing: 2px; color: var(--ink);
  }
  .brand-sub {
    position: absolute; top: 330px; right: 174px;
    font-size: 17px; font-weight: 600; color: var(--brand-green-dark); letter-spacing: 0.5px;
  }
  .product-name {
    position: absolute; top: 362px; width: 100%; text-align: center;
    font-size: 44px; font-weight: 600; letter-spacing: 1px;
    color: var(--brand-green);
  }
  .product-name sup { font-size: 14px; vertical-align: 26px; }
  .product-type {
    position: absolute; top: 420px; left: 95px; right: 95px;
    display: flex; align-items: center; gap: 10px;
    font-size: 27px; font-weight: 400; letter-spacing: 1px; color: var(--ink-soft);
  }
  .product-type .rule { flex: 1; height: 2px; background: var(--brand-green-dark); }
  .dose-pill {
    position: absolute; top: 467px; left: 149px;
    width: 314px; height: 30px; border-radius: 5px;
    background: linear-gradient(90deg, var(--brand-green) 0%, var(--brand-green-dark) 100%);
    color: var(--white); font-size: 16px; font-weight: 500; letter-spacing: 1px;
    display: flex; justify-content: center; align-items: center; gap: 10px;
  }
  .dog-photo {
    position: absolute; left: 250px; top: 540px;
    width: 300px; height: 390px;
    border-radius: 120px 120px 0 0;
    background: radial-gradient(ellipse at 50% 40%, #f4f1ee 0%, #e6e2de 55%, rgba(220,216,212,0) 100%);
  }
  .flavour-badge {
    position: absolute; left: 64px; top: 660px;
    width: 188px; height: 188px; border-radius: 50%;
    background: linear-gradient(150deg, var(--brand-green) 0%, var(--brand-green-dark) 100%);
    color: var(--white); text-align: center;
  }
  .flavour-badge .dash-ring {
    position: absolute; inset: 8px; border-radius: 50%;
    border: 1.5px dashed rgba(255,255,255,0.7);
  }
  .flavour-art {
    position: absolute; left: 62px; top: 26px; width: 64px; height: 70px;
    border-radius: 50%; background: rgba(255,255,255,0.12);
  }
  .flavour-name {
    position: absolute; top: 102px; width: 100%;
    font-size: 22px; font-weight: 700; letter-spacing: 1.5px;
  }
  .flavour-rule {
    position: absolute; top: 132px; left: 52px; right: 52px;
    height: 1px; background: rgba(255,255,255,0.7);
  }
  .flavour-weight {
    position: absolute; top: 138px; width: 100%;
    font-size: 20px; font-weight: 400; letter-spacing: 1px;
  }
  .endorsement {
    position: absolute; left: 82px; top: 860px;
    font-size: 11px; line-height: 1.15; color: var(--ink-soft); letter-spacing: 0.6px;
  }
  .endorsement strong { display: block; font-weight: 700; color: var(--ink); }
  .base-band {
    position: absolute; left: 0; right: 0; bottom: 0; height: 92px;
    background: linear-gradient(90deg, var(--brand-green) 0%, var(--brand-green-dark) 100%);
  }
</style>
</head>
<body>
  <main class="pouch">
    <span class="tear-notch left"></span>
    <span class="tear-notch right"></span>

    <p class="tagline">SUPPORT<span class="sep">|</span>CALM<span class="sep">|</span>EASE</p>
    <div class="zip-line"></div>

    <div class="brand">
      <span class="brand-dot"></span>
      <span class="brand-name">VERDANEL</span>
    </div>
    <p class="brand-sub">For Animals</p>

    <h1 class="product-name">VERDABITES<sup>™</sup></h1>
    <p class="product-type"><span class="rule"></span>CBD TREATS<span class="rule"></span></p>
    <p class="dose-pill"><span>CBD 250MG</span><span>|</span><span>0% THC</span></p>

    <div class="dog-photo" role="img" aria-label="Photograph of the brand ambassador, a cream-coloured wrinkled shar-pei dog in profile"></div>

    <div class="flavour-badge">
      <span class="dash-ring"></span>
      <div class="flavour-art" role="img" aria-label="Line illustration of a chicken drumstick"></div>
      <p class="flavour-name">CHICKEN</p>
      <span class="flavour-rule"></span>
      <p class="flavour-weight">120G</p>
    </div>

    <p class="endorsement">RECOMMENDED BY<strong>VETERINARIANS</strong></p>

    <div class="base-band" role="img" aria-label="Green band with a repeating pattern of small paw prints"></div>
  </main>
</body>
</html>
```